New tech executive consulting company needs professionally branded document templates

We are a new business selling fractional board advisory and go-to-market consulting services into the Technology space. Tessaly Brink are experts in providing high-quality executive-level leaders on a part-time basis to tech companies in need of their expertise. We work closely with clients to understand their business needs, challenges, and goals, and provides customised solutions to help them succeed. Due to our audience we need the design to have a high quality, executive look and feel.

Our first website is live and can be found at tessalybrink.example. We also already have a logo which I've uploaded. Our brand is clean and uses orange to give it colour and an identity that stands out.

We need some document master templates created so we can create our own presentations (Google Slides & Powerpoint), PDF documents, and Word templates, and ideally also a LinkedIn banner.

```html
<!DOCTYPE html>
<html lang="en">
<head>
<meta charset="utf-8">
<title>Tessaly Brink – Presentation Template</title>
<link href="https://fonts.googleapis.com/css2?family=Poppins:wght@300;400;500;600;700&display=swap" rel="stylesheet">
<style>
  :root{
    --page:#c4c4c4;
    --paper:#f1ede6;
    --navy:#28303d;
    --navy-deep:#1e2530;
    --orange:#ef8650;
    --orange-deep:#e4602a;
    --white:#ffffff;
    --body:#3a3f48;
  }
  *{margin:0;padding:0;box-sizing:border-box}
  html,body{width:1200px;height:1072px;overflow:hidden;background:var(--page)}
  body{position:relative;font-family:'Poppins',sans-serif;color:var(--navy)}
  .slide{position:absolute;width:545px;height:306px;overflow:hidden;background:var(--paper)}
  .stage{position:absolute;left:0;top:0;width:925px;height:520px;transform:scale(.5888);transform-origin:0 0}
  .stage > svg.shapes{position:absolute;left:0;top:0;width:925px;height:520px}
  .pos{position:absolute}
  .brand{position:absolute;left:34px;top:30px;font-weight:700;font-size:22px;line-height:25px;letter-spacing:1.5px;text-transform:uppercase;color:var(--navy);text-align:center}
  .brand.light{color:var(--white)}
  .page-no{position:absolute;right:9px;bottom:8px;font-size:11px;font-weight:600;color:var(--white)}
  .heading{font-weight:700;text-transform:uppercase;font-size:28px;line-height:34px;color:var(--navy)}
  .copy{font-weight:300;font-size:9.6px;line-height:19.3px;color:var(--body)}

  /* cover */
  .cover-title{left:31px;top:190px;font-weight:700;font-size:28px;line-height:34px;color:var(--white);text-transform:uppercase}
  .cover-title .accent{color:var(--orange)}

  /* solution */
  .step{position:absolute;display:flex;align-items:center;gap:10px}
  .step .num{font-weight:600;font-size:30px;line-height:30px;color:var(--navy)}
  .step .label{font-weight:600;font-size:15.5px;line-height:15px;color:var(--navy)}
  .step .dot{width:12px;height:12px;border-radius:50%;background:var(--navy)}
  .step-text{position:absolute;font-weight:300;font-size:8.6px;line-height:14.5px;color:var(--body);width:200px}
  .step-text.right{text-align:right}

  /* thank you */
  .thanks{position:absolute;left:320px;width:400px;text-align:center}
  .thanks-title{top:55px;font-weight:700;font-size:50px;line-height:52px;text-transform:uppercase;color:var(--navy)}
  .thanks-lead{top:178px;font-weight:600;font-size:14.5px;line-height:24px;color:var(--navy)}
  .contact{position:absolute;width:260px;margin-left:-130px;text-align:center}
  .contact .icon{display:block;width:36px;height:36px;margin:0 auto 12px;border-radius:50%;background:var(--orange)}
  .contact .icon svg{width:36px;height:36px;display:block}
  .contact .value{font-weight:600;font-size:14.5px;color:var(--navy)}
</style>
</head>
<body>

<!-- Slide 01 : cover -->
<section class="slide" style="left:38px;top:45px">
  <div class="stage">
    <svg class="shapes" viewBox="0 0 925 520">
      <defs>
        <linearGradient id="meetingTone" x1="0" y1="0" x2="1" y2="1">
          <stop offset="0" stop-color="#1a212b"/>
          <stop offset=".55" stop-color="#2a3340"/>
          <stop offset="1" stop-color="#3a3a3c"/>
        </linearGradient>
      </defs>
      <rect width="925" height="520" fill="url(#meetingTone)" role="img" aria-label="Photo of a business team meeting around a table"/>
      <g fill="#e9834f" opacity=".82">
        <polygon points="660,0 715,0 350,520 295,520"/>
        <polygon points="760,0 790,0 430,520 400,520"/>
        <polygon points="840,0 925,0 925,20 560,520 480,520"/>
        <polygon points="925,150 925,260 740,520 660,520"/>
      </g>
      <polygon points="875,520 925,470 925,520" fill="var(--orange)"/>
    </svg>
    <div class="brand light">Tessaly<br>Brink</div>
    <h1 class="pos cover-title">Experts in providing<br><span class="accent">executive leadership</span><br>on demand</h1>
    <span class="page-no">01</span>
  </div>
</section>

<!-- Slide 04 : our solution -->
<section class="slide" style="left:618px;top:45px">
  <div class="stage">
    <svg class="shapes" viewBox="0 0 925 520">
      <defs>
        <linearGradient id="triOrange" x1="0" y1="0" x2="0" y2="1">
          <stop offset="0" stop-color="#f4a06c"/>
          <stop offset="1" stop-color="var(--orange-deep)"/>
        </linearGradient>
        <linearGradient id="officeTone" x1="0" y1="0" x2="0" y2="1">
          <stop offset="0" stop-color="#8a6a4d"/>
          <stop offset=".6" stop-color="#b98a5e"/>
          <stop offset="1" stop-color="#5c6470"/>
        </linearGradient>
      </defs>
      <polygon points="463,134 784,520 141,520" fill="url(#triOrange)"/>
      <polygon points="463,160 680,520 250,520" fill="url(#officeTone)" role="img" aria-label="Photo of a smiling woman holding a laptop in an office"/>
      <polygon points="875,520 925,470 925,520" fill="var(--orange)"/>
    </svg>
    <div class="brand">Tessaly<br>Brink</div>
    <h2 class="pos heading" style="right:40px;top:30px">Our solution</h2>

    <div class="step" style="right:480px;top:107px"><span class="label">Nemo enim ipsam</span><span class="num">03</span><span class="dot"></span></div>
    <p class="step-text right" style="right:555px;top:142px">Lorem ipsum dolor sit amet, consectetur adipisc ing elit, sed do eiusmod tempor incididunt ut labore et dolore magna aliqua.</p>

    <div class="step" style="left:482px;top:107px"><span class="dot"></span><span class="num">04</span><span class="label">Nemo enim ipsam</span></div>
    <p class="step-text" style="left:555px;top:142px">Lorem ipsum dolor sit amet, consectetur adipisc ing elit, sed do eiusmod tempor incididunt ut labore et dolore magna aliqua.</p>

    <div class="step" style="right:600px;top:244px"><span class="label">Nemo enim ipsam</span><span class="num">02</span><span class="dot"></span></div>
    <p class="step-text right" style="right:675px;top:279px">Lorem ipsum dolor sit amet, consectetur adipisc ing elit, sed do eiusmod tempor incididunt ut labore et dolore magna aliqua.</p>

    <div class="step" style="left:602px;top:244px"><span class="dot"></span><span class="num">05</span><span class="label">Nemo enim ipsam</span></div>
    <p class="step-text" style="left:675px;top:279px">Lorem ipsum dolor sit amet, consectetur adipisc ing elit, sed do eiusmod tempor incididunt ut labore et dolore magna aliqua.</p>

    <div class="step" style="right:720px;top:380px"><span class="label" style="text-align:right">Nemo enim<br>ipsam</span><span class="num">01</span><span class="dot"></span></div>
    <p class="step-text right" style="right:794px;top:425px;width:115px">Lorem ipsum dolor sit amet, consectetur adipisc ing elit, sed do eiusmod</p>

    <div class="step" style="left:722px;top:380px"><span class="dot"></span><span class="num">06</span><span class="label">Nemo enim<br>ipsam</span></div>
    <p class="step-text" style="left:797px;top:425px;width:115px">Lorem ipsum dolor sit amet, consectetur adipisc ing elit, sed do eiusmod</p>

    <span class="page-no">04</span>
  </div>
</section>

<!-- Slide 02 : smart way -->
<section class="slide" style="left:38px;top:380px">
  <div class="stage">
    <svg class="shapes" viewBox="0 0 925 520">
      <defs>
        <linearGradient id="teamTone" x1="0" y1="0" x2="1" y2="1">
          <stop offset="0" stop-color="#6b4a36"/>
          <stop offset=".5" stop-color="#a8a29a"/>
          <stop offset="1" stop-color="#4c5768"/>
        </linearGradient>
      </defs>
      <polygon points="925,83 925,520 460,520 460,412 605,310 862,310 862,125" fill="var(--orange)"/>
      <polygon points="0,83 612,520 0,520" fill="var(--navy)"/>
      <rect x="35" y="233" width="371" height="247" fill="url(#teamTone)" role="img" aria-label="Photo of a team discussing work at a meeting table"/>
      <polygon points="875,520 925,470 925,520" fill="var(--navy-deep)"/>
    </svg>
    <div class="brand">Tessaly<br>Brink</div>
    <h2 class="pos heading" style="left:449px;top:43px">The smart way to<br>scale your business</h2>
    <div class="pos copy" style="left:449px;top:124px;width:398px">
      <p>Tessaly Brink are experts in providing high-quality executive-level leaders on a part-time basis to tech companies in need of their expertise. We work closely with clients to understand their business needs, challenges, and goals, and provides customised solutions to help them succeed.</p>
      <p style="margin-top:19px">Our strategic insights, leadership, and collaborative approach make us a valuable partner for companies looking to drive growth and innovation. We are passionate about helping companies achieve their goals and are committed to providing the highest level of service to our clients.</p>
    </div>
    <span class="page-no">02</span>
  </div>
</section>

<!-- Slide 05 : location -->
<section class="slide" style="left:618px;top:380px">
  <div class="stage">
    <svg class="shapes" viewBox="0 0 925 520">
      <polygon points="707,0 790,0 925,200 925,330" fill="var(--orange)"/>
      <polygon points="0,228 0,340 115,520 195,520" fill="var(--orange)"/>
      <rect x="185" y="110" width="215" height="345" rx="30" fill="var(--navy)" role="img" aria-label="Map of the United Kingdom with a location marker in the south"/>
      <polygon points="875,520 925,470 925,520" fill="var(--orange)"/>
    </svg>
    <div class="brand">Tessaly<br>Brink</div>
    <h2 class="pos heading" style="left:492px;top:205px">Our location</h2>
    <p class="pos" style="left:492px;top:258px;width:332px;font-weight:300;font-size:8.4px;line-height:14.4px;text-align:justify;color:var(--body)">Lorem ipsum dolor sit amet, consectetur adipiscing elit, sed do eiusmod tempor incididunt ut labore et dolore magna aliqua. Ut enim ad minim veniam, quis nostrud exercitation ullamco laboris nisi ut aliquip ex ea commodo consequat. Duis aute irure dolor in reprehenderit in voluptate velit esse cillum dolore eu fugiat nulla pariatur. Excepteur sint occaecat cupidatat non proident, sunt in culpa qui officia deserunt mollit anim id est laborum.</p>
    <span class="page-no">05</span>
  </div>
</section>

<!-- Slide 03 : founder -->
<section class="slide" style="left:38px;top:721px">
  <div class="stage">
    <svg class="shapes" viewBox="0 0 925 520">
      <defs>
        <linearGradient id="portraitTone" x1="0" y1="0" x2="0" y2="1">
          <stop offset="0" stop-color="#7a5a40"/>
          <stop offset=".55" stop-color="#c79a7c"/>
          <stop offset="1" stop-color="#2f4a78"/>
        </linearGradient>
      </defs>
      <rect x="470" y="0" width="180" height="520" fill="var(--orange)"/>
      <rect x="551" y="76" width="273" height="367" fill="var(--white)"/>
      <rect x="565" y="88" width="273" height="343" fill="url(#portraitTone)" role="img" aria-label="Portrait photo of the founder in a blue blazer"/>
      <polygon points="875,520 925,470 925,520" fill="var(--orange)"/>
    </svg>
    <div class="brand">Tessaly<br>Brink</div>
    <h2 class="pos heading" style="left:34px;top:160px">Rowan Pell</h2>
    <div class="pos copy" style="left:35px;top:210px;width:388px;text-align:justify">
      <p>Rowan Pell is a highly accomplished business leader with extensive experience in executive-level leadership and strategy. As the founder of Tessaly Brink, Rowan brings years of experience in the technology industry to help companies achieve their goals.</p>
      <p style="margin-top:19px">Throughout their career, Rowan has held executive positions in companies ranging from startups to large corporations, with a deep understanding of the tech industry, and has helped companies at all stages of maturity drive significant growth and innovation.</p>
    </div>
    <span class="page-no">03</span>
  </div>
</section>

<!-- Slide 06 : thank you -->
<section class="slide" style="left:618px;top:721px">
  <div class="stage">
    <svg class="shapes" viewBox="0 0 925 520">
      <defs>
        <linearGradient id="warmTone" x1="0" y1="0" x2="1" y2="1">
          <stop offset="0" stop-color="#5a3a26"/>
          <stop offset=".5" stop-color="#c9703c"/>
          <stop offset="1" stop-color="#e8864d"/>
        </linearGradient>
      </defs>
      <polygon points="212,0 340,0 0,510 0,330" fill="url(#warmTone)" role="img" aria-label="Photo of a professional woman working, toned orange"/>
      <polygon points="880,0 925,0 925,70 645,520 540,520" fill="url(#warmTone)" role="img" aria-label="Photo of colleagues at a desk, toned orange"/>
      <polygon points="875,520 925,470 925,520" fill="var(--orange)"/>
    </svg>
    <div class="brand">Tessaly<br>Brink</div>
    <h2 class="thanks thanks-title">Thank<br>you!</h2>
    <p class="thanks thanks-lead">Let us help you take your business to the next level.<br>Contact us for a free consultation.</p>

    <div class="contact" style="left:427px;top:244px">
      <span class="icon"><svg viewBox="0 0 36 36"><rect x="11" y="13" width="14" height="10" rx="1.5" fill="#fff"/><polyline points="11,14 18,19 25,14" fill="none" stroke="var(--orange)" stroke-width="1.4"/></svg></span>
      <span class="value">info@tessalybrink.example</span>
    </div>
    <div class="contact" style="left:340px;top:333px">
      <span class="icon"><svg viewBox="0 0 36 36"><path d="M13.5 11.5c.6-.6 1.5-.6 2 0l1.6 2c.4.5.4 1.2-.1 1.7l-1 1c.8 1.7 2.1 3 3.8 3.8l1-1c.5-.5 1.2-.5 1.7-.1l2 1.6c.6.5.6 1.4 0 2l-1 1c-.9.9-2.2 1.1-3.3.6-3.3-1.5-5.9-4.1-7.4-7.4-.5-1.1-.3-2.4.6-3.3z" fill="#fff"/></svg></span>
      <span class="value">+44 7700 900123</span>
    </div>
    <div class="contact" style="left:244px;top:422px">
      <span class="icon"></span>
      <span class="value">Rowan Pell</span>
    </div>
    <span class="page-no">06</span>
  </div>
</section>

</body>
</html>
```